Web Design Project

i'm looking for a sleek modern design i can use for a web site that deals with.
Intelligent Data Capture
Accounts Payable Solutions for faster processing based on our scanning solution.
ultimately we are a intelligent scanning software.

here is a great website, that does exactly what we do, and we like to have most of their services and products.

so something in this idea would be great.
www.valtrino.com

so i guess i want a good landing/home page which is smartly designed so users will be inclined to leave their information.

and then information pages.

also i dont need any cms for you to include, i only need you to hook the html hooks for RANK Kettle as i already have a CMS and need it to hook in to that, i am including links to that cheat sheet.
so it is easier when included as you create the Theme.

http://www.rankkettle.com/how-to-create-website-template.html
http://www.rankkettle.com/cheat-sheet.html
Updates

Hi Guys sorry for the long pause in design, but here is where we stand.

what ever design i choose, i need that designer to customize a few things for me based on design that was designed.
and i will need designer to match that them to work with RANK Kettle
here is the cheat sheet for the hooks that we need to match and make it work.
if you have any questions let me know.

otherwise i look forward to working with you. and good luck.

Target Market(s)

CFO's AP Managers, mostly ppl who are not Tech freindly

Industry/Entity Type

Software

Requirements
Must have
• i need on home page, the rotating banner should have 1 ability to place youtube links to show videos, and also ability to add buttons on these rotating banners that will allow forms to pop up take to another page.

```html
<!DOCTYPE html>
<html lang="en">
<head>
<meta charset="utf-8">
<title>KERN – Intelligent Data Capture</title>
<link rel="stylesheet" href="https://fonts.googleapis.com/css2?family=Ubuntu:wght@300;400;500&family=Ubuntu+Condensed&display=swap">
<style>
:root{
  --brand:#1b6fa8;
  --nav-dark:#0f1d28;
  --text:#333;
  --muted:#666;
  --line:#d4d4d4;
  --accent-sky:#2e9fdf;
  --accent-deep:#1d5fa8;
  --link-red:#9b1c1c;
  --orange:#f39a12;
  --footer-bg:#f1f1f1;
  --footer-bar:#d9d9d9;
  --panel:#ececec;
}
*{box-sizing:border-box;margin:0;padding:0}
html,body{width:843px;height:1200px;overflow:hidden;background:#fff}
body{font-family:"Ubuntu",sans-serif;color:var(--text)}
.page{position:relative;width:843px;height:1200px}
.abs{position:absolute}

/* header */
.site-header{left:11px;top:5px;width:824px;height:105px;border:1px solid var(--line);border-radius:4px;background:#fff}
.brand-name{left:40px;top:24px;font-size:36px;font-weight:400;color:var(--brand);letter-spacing:0.5px}
.search{left:619px;top:15px;width:167px;height:18px;background:#f3f3f3;border:1px solid #e2e2e2;font-size:9px;color:#777;padding:3px 11px}
.search svg{position:absolute;right:6px;top:4px}
.main-nav{left:347px;top:61px;display:flex;align-items:center;height:39px;font-size:12px;color:#333}
.main-nav a{color:inherit;text-decoration:none;padding:0 13px;line-height:39px;border-right:1px solid #ececec}
.main-nav a:last-child{border-right:0}
.main-nav a.current{background:var(--nav-dark);color:#fff;border-radius:3px;padding:0 27px;border-right:0}

/* hero */
.hero{left:11px;top:118px;width:824px;height:278px;border-radius:4px;overflow:hidden;
  background:linear-gradient(100deg,#1e8fd8 0%,#3aaeea 35%,#bcdff2 58%,#8a8f93 78%,#5c5650 100%)}
.hero-title{left:48px;top:64px;font-size:25px;color:#fff;font-weight:400}
.hero-text{left:52px;top:112px;width:300px;font-size:10.5px;line-height:17px;color:#fff}
.hero-btn{left:259px;top:189px;width:85px;height:22px;background:#3ba9e3;border:1px solid #6cc3ee;border-radius:2px;color:#fff;font-size:10px;font-weight:500;line-height:20px;text-align:center}
.hero-dots{left:240px;top:250px;display:flex;gap:3px}
.hero-dots span{width:8px;height:8px;border-radius:50%;background:#fff}
.hero-dots span.off{background:#1b4c7a;border:2px solid #fff}

/* service columns */
.service{top:421px;width:252px}
.service h2{font-family:"Ubuntu Condensed",sans-serif;font-weight:400;font-size:16px;color:#333;margin-left:4px}
.service .thumb{position:relative;margin-top:10px;height:102px;border:4px solid #e3eef6;border-radius:3px}
.service .thumb .photo{position:absolute;inset:0}
.service .thumb .dl{position:absolute;right:0;bottom:0;width:78px;height:31px;background:rgba(40,40,40,.75);color:#fff;font-family:"Ubuntu Condensed",sans-serif;font-size:14px;line-height:31px;text-align:center}
.service p{margin:12px 9px 0;font-size:9px;line-height:15px;color:#444}
.service .more{margin-top:11px;height:22px;background:var(--panel);border-radius:2px;font-family:"Ubuntu Condensed",sans-serif;font-size:11px;color:#555;padding:3px 9px;position:relative}
.service .more svg{position:absolute;right:18px;top:8px}

/* welcome */
.welcome-title{left:31px;top:664px;font-size:23px;font-weight:300;color:var(--accent-sky)}
.welcome-title span{color:#888;font-size:20px}
.welcome-text{left:31px;top:706px;width:512px;font-size:10px;line-height:16.5px;color:#777}
.welcome-more{left:474px;top:808px;font-size:10px;color:var(--link-red)}
.video{left:581px;top:686px;width:227px;height:129px;border:2px solid #222;background:linear-gradient(120deg,#d9d9d9,#8d9aa3)}
.video .bar{position:absolute;left:0;right:0;bottom:0;height:13px;background:#1b1b1b}
.video .progress{position:absolute;left:0;bottom:13px;height:3px;width:100%;background:#555}
.video .progress i{display:block;width:28%;height:100%;background:#c4161c}
.video .play{position:absolute;left:98px;top:50px}

/* partners */
.partners-label{left:37px;top:837px;font-size:13px;color:var(--accent-deep)}
.partner-arrows{left:779px;top:834px}
.partners{left:18px;top:866px;width:812px;height:99px;border:1px solid #cfcfcf;border-radius:3px;box-shadow:0 1px 3px rgba(0,0,0,.15);display:flex;align-items:center;justify-content:space-around;padding:0 20px}
.partner-badge{height:50px;border-radius:4px}

/* footer */
.footer{left:0;top:1007px;width:843px;height:158px;background:var(--footer-bg)}
.footer h3{position:absolute;font-weight:400;font-size:13.5px;color:#222}
.footer .small{position:absolute;font-size:8.5px;line-height:14px;color:#222}
.email-field{left:36px;top:88px;width:222px;height:21px;background:#fff;border:0;font-size:8px;font-style:italic;color:#999;padding:5px 8px;box-shadow:0 4px 4px -3px rgba(0,0,0,.2)}
.subscribe{left:183px;top:116px;width:70px;height:23px;background:var(--orange);border:1px solid #d97f00;border-radius:3px;color:#fff;font-size:10px;font-weight:500;line-height:21px;text-align:center}
.social{left:607px;top:60px;display:flex;gap:16px}
.social span{width:17px;height:17px;background:#8e9aa6;border-radius:2px}
.footer-bar{left:0;top:1165px;width:843px;height:35px;background:var(--footer-bar);font-size:8.5px;color:#444;text-align:center;line-height:35px}
</style>
</head>
<body>
<div class="page">

  <header class="abs site-header">
    <div class="abs brand-name">KERN</div>
    <div class="abs search">Search Here
      <svg width="9" height="9" viewBox="0 0 10 10"><circle cx="4" cy="4" r="3" fill="none" stroke="#333" stroke-width="1.3"/><line x1="6" y1="6" x2="9" y2="9" stroke="#333" stroke-width="1.6"/></svg>
    </div>
    <nav class="abs main-nav">
      <a class="current" href="#">Home</a>
      <a href="#">About Us</a>
      <a href="#">Services</a>
      <a href="#">Testimonials</a>
      <a href="#">Blog</a>
      <a href="#">Contact</a>
    </nav>
  </header>

  <section class="abs hero" role="img" aria-label="Hands inserting an access card into a card reader connected to a phone">
    <h1 class="abs hero-title">Data capture from online sites</h1>
    <p class="abs hero-text">Lorem ipsum dolor sit amet, consectetur adipiscing elit. ipsum dolor sit amet.Lorem ipsum dolor sit amet, consectetur adipiscing elit. ipsum dolor sit amet.</p>
    <div class="abs hero-btn">Learn more &nbsp;›</div>
    <div class="abs hero-dots"><span></span><span></span><span class="off"></span></div>
  </section>

  <article class="abs service" style="left:18px">
    <h2>Electronic Document Systems</h2>
    <div class="thumb"><div class="photo" role="img" aria-label="Finger touching glowing digital panels" style="background:linear-gradient(120deg,#0b2f4a,#2b7fb0 50%,#0d3552)"></div><div class="dl">Download</div></div>
    <p>Fusce accumsan, elit a suscipit sagittis, tortor sapien cursus risus, non rhoncus nunc ac elit. Fusce accum-san, elit a suscipit sagittis, tortor sapien cursus risus,</p>
    <div class="more">View More<svg width="58" height="6" viewBox="0 0 58 6"><line x1="0" y1="3" x2="57" y2="3" stroke="#555" stroke-width=".8"/><polyline points="54,0.5 57,3 54,5.5" fill="none" stroke="#555" stroke-width=".8"/></svg></div>
  </article>

  <article class="abs service" style="left:299px">
    <h2>Online Backup &amp; Disaster Recovery</h2>
    <div class="thumb"><div class="photo" role="img" aria-label="Businesswoman reading her phone" style="background:linear-gradient(90deg,#f4f4f4,#c9ccd0 55%,#eeeeee)"></div><div class="dl">Download</div></div>
    <p>Fusce accumsan, elit a suscipit sagittis, tortor sapien cursus risus, non rhoncus nunc ac elit. Fusce accum-san, elit a suscipit sagittis, tortor sapien cursus risus,</p>
    <div class="more">View More<svg width="58" height="6" viewBox="0 0 58 6"><line x1="0" y1="3" x2="57" y2="3" stroke="#555" stroke-width=".8"/><polyline points="54,0.5 57,3 54,5.5" fill="none" stroke="#555" stroke-width=".8"/></svg></div>
  </article>

  <article class="abs service" style="left:580px">
    <h2>Information Capture Services</h2>
    <div class="thumb"><div class="photo" role="img" aria-label="Smartphone and pen resting on printed documents" style="background:linear-gradient(120deg,#2a2a2a,#8c8c8c 45%,#e8e8e8)"></div><div class="dl">Download</div></div>
    <p>Fusce accumsan, elit a suscipit sagittis, tortor sapien cursus risus, non rhoncus nunc ac elit. Fusce accum-san, elit a suscipit sagittis, tortor sapien cursus risus,</p>
    <div class="more">View More<svg width="58" height="6" viewBox="0 0 58 6"><line x1="0" y1="3" x2="57" y2="3" stroke="#555" stroke-width=".8"/><polyline points="54,0.5 57,3 54,5.5" fill="none" stroke="#555" stroke-width=".8"/></svg></div>
  </article>

  <h2 class="abs welcome-title">Welcome to <span>KERN</span></h2>
  <p class="abs welcome-text">Sed ut perspiciatis unde omnis iste natus error sit voluptatem accusantium doloremque laudantium, totam rem aperiam, eaque ipsa quae ab illo inventore veritatis et quasi architecto beatae vitae dicta sunt explicabo. Nemo enim ipsam voluptatem quia voluptas sit aspernatur aut odit aut fugit, sed quia consequuntur magni dolores eos qui ratione voluptatem sequi nesciunt. Neque porro quisquam est, qui dolorem ipsum quia dolor sit amet, consectetur, adipisci velit, sed quia non numquam eius modi tempora incidunt ut labore et dolore magnam aliquam quaerat voluptatem aliquid ex ea commodi consequatur.</p>
  <div class="abs welcome-more">View More &nbsp;&gt;&gt;</div>

  <div class="abs video" role="img" aria-label="Video player showing a woman in an office">
    <svg class="play" width="26" height="18" viewBox="0 0 26 18"><rect width="26" height="18" rx="2" fill="#111"/><polygon points="10,4 18,9 10,14" fill="#fff"/></svg>
    <div class="progress"><i></i></div>
    <div class="bar"></div>
  </div>

  <div class="abs partners-label">Partners</div>
  <svg class="abs partner-arrows" width="34" height="20" viewBox="0 0 34 20"><polygon points="13,1 3,10 13,19" fill="#555"/><polygon points="21,1 31,10 21,19" fill="#555"/></svg>
  <div class="abs partners">
    <div class="partner-badge" style="width:78px;background:#8cc63f"></div>
    <div class="partner-badge" style="width:150px;background:#d3d7db"></div>
    <div class="partner-badge" style="width:56px;background:#3340a8"></div>
    <div class="partner-badge" style="width:56px;background:#2a8fd0"></div>
    <div class="partner-badge" style="width:84px;background:#f08a24"></div>
    <div class="partner-badge" style="width:86px;background:#c6cf3a"></div>
  </div>

  <footer class="abs footer">
    <h3 style="left:36px;top:33px">Sign Up to Stay in Touch</h3>
    <p class="small" style="left:36px;top:58px;width:200px">Please enter your email address below to sign up for our mailing list.</p>
    <div class="abs email-field">your email address here..</div>
    <div class="abs subscribe">Subscribe ›</div>

    <h3 style="left:375px;top:28px">Contact Info</h3>
    <p class="small" style="left:376px;top:55px;line-height:17px">Loreum Ipsum dollar<br>Lakemont, OR 97015</p>
    <p class="small" style="left:376px;top:98px;line-height:17px">Phone: <span style="font-size:10px">555-014-2290</span><br>Email : info@ kernscan.com</p>

    <h3 style="left:607px;top:28px">Follow Us</h3>
    <div class="abs social" aria-label="Social links"><span></span><span></span><span></span><span></span><span></span></div>
    <p class="small" style="left:612px;top:103px">Privay Policy &nbsp;| &nbsp;Terms of Use</p>
  </footer>

  <div class="abs footer-bar">© 2013 KERN &nbsp;| &nbsp;All right reserved</div>
</div>
</body>
</html>
```